Skyborne Ridge Flights
Private Charters
Skyborne Ridge Flights  - Aviation
Creative Brief
Cutting-Edge
Dorothy Kalloway
Business Development
5291 N. Brantley, Suite 240 Scottsdale, AZ 85254
tkalloway@skyborneridgeflights.example
www.skyborneridgeflights.example

```html
<!DOCTYPE html>
<html lang="en">
<head>
<meta charset="utf-8">
<title>Skyborne Ridge Flights – Stationery</title>
<link href="https://fonts.googleapis.com/css2?family=Cinzel:wght@400;600&family=Open+Sans:wght@400;600&display=swap" rel="stylesheet">
<style>
  :root{
    --bg:#e4e4e4;
    --paper:#ffffff;
    --brown:#7a3a22;
    --brown-dark:#5e2a16;
    --brown-light:#a4552f;
    --ink:#4a4a4a;
    --shadow:0 1px 4px rgba(0,0,0,.18);
  }
  *{box-sizing:border-box;margin:0;padding:0}
  html,body{width:1200px;height:854px;overflow:hidden}
  body{background:var(--bg);position:relative;font-family:"Open Sans",Arial,sans-serif;color:var(--ink)}

  .brand{display:flex;align-items:center;gap:7px;font-family:"Cinzel",Georgia,serif;font-weight:400;color:var(--brown);letter-spacing:.5px;white-space:nowrap}
  .brand__square{width:10px;height:10px;background:currentColor;flex:none}
  .brand--light{color:#fff}

  .contact{position:absolute;font-style:normal;font-size:5.6px;line-height:8px;color:var(--ink)}
  .web{position:absolute;font-size:5.6px;color:var(--brown)}

  /* Letterhead */
  .letterhead{position:absolute;left:67px;top:29px;width:492px;height:789px;background:var(--paper);box-shadow:var(--shadow)}
  .letterhead .brand{position:absolute;left:24px;top:34px;font-size:17px}
  .letterhead .contact{left:22px;bottom:24px;border-left:1px solid var(--brown);padding-left:4px}
  .letterhead .web{right:24px;bottom:22px}
  .letterhead__band{position:absolute;left:18px;right:18px;bottom:10px;height:9px;background:linear-gradient(90deg,var(--brown-dark),var(--brown-light) 50%,var(--brown-dark))}

  /* Business card */
  .card{position:absolute;top:65px;width:197px;height:130px;border-radius:7px;box-shadow:var(--shadow);overflow:hidden}
  .card--front{left:600px;background:var(--paper)}
  .card--front .brand{position:absolute;left:12px;top:12px;width:80px;flex-direction:column;align-items:center;gap:3px;font-size:7px;line-height:1.2;text-align:center;white-space:normal}
  .card--front .brand__square{width:6px;height:6px}
  .card__person{position:absolute;right:14px;top:17px;width:84px;text-align:center}
  .card__name{font-size:7.6px;color:var(--brown);font-weight:600;white-space:nowrap}
  .card__role{font-size:5.3px;color:var(--ink);white-space:nowrap}
  .card--front .contact{left:12px;top:52px;font-size:5px;line-height:7.4px;border-left:1px solid var(--brown);padding-left:3px}
  .card__band{position:absolute;left:0;right:0;bottom:0;height:13px;background:linear-gradient(90deg,var(--brown-dark),var(--brown-light))}
  .card__band .web{right:10px;top:3px;color:#fff;font-size:5px}
  .card--back{left:816px;background:radial-gradient(circle at 50% 40%,var(--brown-light),var(--brown) 70%)}
  .card--back .brand{position:absolute;left:50%;top:50%;transform:translate(-50%,-50%);font-size:9px;gap:5px}
  .card--back .brand__square{width:7px;height:7px}

  /* Envelopes */
  .envelope{position:absolute;left:595px;width:564px;background:var(--paper);box-shadow:var(--shadow)}
  .envelope--front{top:216px;height:281px}
  .envelope--front .brand{position:absolute;left:24px;top:28px;font-size:12px}
  .envelope--front .contact{left:6px;bottom:17px;border-left:1px solid var(--brown);padding-left:4px}
  .envelope__band{position:absolute;left:0;right:0;bottom:0;height:9px;background:linear-gradient(90deg,var(--brown-dark),var(--brown-light) 50%,var(--brown-dark))}
  .envelope--front .web{right:10px;bottom:11px}
  .envelope--back{top:523px;height:269px}
  .envelope__flap{position:absolute;left:0;top:0;width:564px;height:96px}
  .envelope--back .brand{position:absolute;left:50%;top:34px;transform:translateX(-50%);font-size:12px}
</style>
</head>
<body>

<section class="letterhead">
  <div class="brand"><span class="brand__square"></span>Skyborne Ridge Flights</div>
  <address class="contact">
    5291 N. Brantley, Suite 240<br>
    Scottsdale, AZ 85254<br>
    Phone: 480.555.0142<br>
    Fax: 480.555.0143<br>
    Toll Free: 800.555.0190<br>
    tkalloway@skyborneridgeflights.example
  </address>
  <span class="web">www.skyborneridgeflights.example</span>
  <div class="letterhead__band"></div>
</section>

<section class="card card--front">
  <div class="brand"><span class="brand__square"></span><span>Skyborne Ridge<br>Flights</span></div>
  <div class="card__person">
    <div class="card__name">Dorothy Kalloway</div>
    <div class="card__role">Business Development</div>
  </div>
  <address class="contact">
    5291 N. Brantley, Suite 240<br>
    Scottsdale, AZ 85254<br>
    Phone: 480.555.0142<br>
    Mobile: 480.555.0177<br>
    Fax: 480.555.0143<br>
    tkalloway@skyborneridgeflights.example
  </address>
  <div class="card__band"><span class="web">www.skyborneridgeflights.example</span></div>
</section>

<section class="card card--back">
  <div class="brand brand--light"><span class="brand__square"></span>Skyborne Ridge Flights</div>
</section>

<section class="envelope envelope--front">
  <div class="brand"><span class="brand__square"></span>Skyborne Ridge Flights</div>
  <address class="contact">
    5291 N. Brantley, Suite 240<br>
    Scottsdale, AZ 85254<br>
    Phone: 480.555.0142<br>
    Fax: 480.555.0143<br>
    tkalloway@skyborneridgeflights.example
  </address>
  <span class="web">www.skyborneridgeflights.example</span>
  <div class="envelope__band"></div>
</section>

<section class="envelope envelope--back">
  <svg class="envelope__flap" viewBox="0 0 564 96" aria-hidden="true">
    <defs>
      <linearGradient id="flapFill" x1="0" x2="1" y1="0" y2="0">
        <stop offset="0" stop-color="#5e2a16"/>
        <stop offset=".5" stop-color="#a4552f"/>
        <stop offset="1" stop-color="#5e2a16"/>
      </linearGradient>
    </defs>
    <path d="M0 0H564V60Q564 70 550 72L300 94Q282 96 264 94L14 72Q0 70 0 60Z" fill="url(#flapFill)"/>
  </svg>
  <div class="brand brand--light"><span class="brand__square"></span>Skyborne Ridge Flights</div>
</section>

</body>
</html>
```